LoopVane - A ride hailing server VAR

our Brindle.co profile: https://brindle.co/517loopvane

LOOPVANE offers first world solutions to first world problems. These days, our smartphones are our cameras, our wallets and our ride home. LOOPVANE guarantees that even if your phone is lost or dies, you'll never get stranded again. Simply call or text (SMS) our toll-free number to request a ride, and choose from one of the various services you subscribe to. LOOPVANE verifies your identity through a unique pin, making it possible to request rides through your own account from a stranger's phone via text or phone call. You can also login through our website or our App, making it easier than ever to get home phoneless.

LOOPVANE is a heterogeneous ride-hailing service that allows users for request transportation from any "transportation network company," taxi, helicopter service, jet service or any transportation service company that is publicly available. LOOPVANE will allow users to connect through our site, automated phone system, App or any appropriated touch point available.

Target Market(s)

RIde Haling

Coding

Coded - Design and coding required

Number of Pages Required

4 page

Requirements
Must have
• hav
Nice to have
• e the same functionality as our competitor's site: https://hopquill.com/
Should not have
• should not be cheezy
• We need to have the registration/sign up on the main page like https://www.zarvix.com/

```html
<!DOCTYPE html>
<html lang="en">
<head>
<meta charset="utf-8">
<title>LoopVane – Ride Anywhere</title>
<link href="https://fonts.googleapis.com/css2?family=Open+Sans:wght@400;600;700;800&display=swap" rel="stylesheet">
<style>
  :root{
    --orange:#f7a51c;
    --orange-dark:#e8920a;
    --ink:#2b2b2b;
    --text:#6b6b6b;
    --muted:#9a9a9a;
    --line:#e3e3e3;
    --soft:#f3f3f3;
    --footer:#1f1a17;
    --white:#ffffff;
  }
  *{box-sizing:border-box;margin:0;padding:0}
  html,body{width:684px;height:1200px;overflow:hidden;background:var(--white)}
  body{font-family:"Open Sans",Arial,sans-serif;color:var(--text);position:relative}

  /* Header */
  .site-header{height:46px;display:flex;align-items:center;justify-content:space-between;padding:0 26px;background:var(--white)}
  .brand{display:flex;align-items:center;gap:7px;font-weight:700;font-size:17px;color:var(--ink)}
  .brand-square{width:22px;height:22px;background:var(--orange);border-radius:4px}
  .main-nav{display:flex;align-items:center;gap:22px;font-size:8.5px;font-weight:600;color:var(--ink);letter-spacing:.4px}
  .btn{display:inline-block;background:var(--orange);color:var(--white);font-weight:700;letter-spacing:.5px;border-radius:2px}
  .btn-nav{font-size:8px;padding:5px 11px}

  /* Hero */
  .hero{position:relative;height:344px;overflow:hidden}
  .hero-art{position:absolute;inset:0;background:linear-gradient(180deg,#fafafa 0%,#e9e9e9 55%,#cfcfcf 80%,#bdbdbd 100%)}
  .hero-copy{position:absolute;top:34px;left:0;right:0;text-align:center}
  .hero-title{font-size:30px;font-weight:800;color:var(--ink);letter-spacing:-.3px}
  .hero-sub{font-size:18px;font-weight:700;color:var(--orange);margin-top:2px}
  .btn-hero{font-size:9px;padding:7px 16px;margin-top:12px}
  .hero-arrow{position:absolute;top:196px;width:14px;height:20px}
  .hero-arrow.left{left:64px}
  .hero-arrow.right{right:64px}

  /* Welcome */
  .welcome{height:225px;padding-top:26px;text-align:center}
  .section-title{font-size:22px;font-weight:600;color:var(--ink)}
  .welcome-text{width:560px;margin:12px auto 0;font-size:8.5px;line-height:1.6;text-align:left}
  .features{display:flex;justify-content:center;gap:28px;margin-top:30px}
  .feature{display:flex;align-items:flex-start;gap:10px;width:170px;text-align:left}
  .feature-icon{flex:none;width:42px;height:42px;border:2px solid var(--orange);border-radius:50%;display:flex;align-items:center;justify-content:center}
  .feature-title{font-size:11.5px;font-weight:700;color:var(--ink)}
  .feature-text{font-size:7px;line-height:1.5;color:var(--muted);margin-top:3px}

  /* Why choose us */
  .why{position:relative;height:285px;border-top:1px solid var(--line);overflow:hidden}
  .why-photo{position:absolute;top:0;right:0;width:440px;height:100%;background:linear-gradient(90deg,rgba(255,255,255,1) 0%,rgba(236,226,210,.6) 30%,#d7c7ad 55%,#e8cf62 85%,#d9b83a 100%)}
  .why-copy{position:relative;padding:36px 0 0 28px;width:270px}
  .why-copy .section-title{font-size:21px;text-align:left}
  .why-text{font-size:8px;line-height:1.65;margin-top:12px}
  .btn-why{font-size:8px;padding:6px 13px;margin-top:16px}

  /* Testimonials */
  .testimonials{height:220px;background:var(--soft);padding-top:20px;text-align:center}
  .testimonials .section-title{font-size:21px;color:var(--orange)}
  .testimonial-list{display:flex;justify-content:center;gap:20px;margin-top:14px}
  .testimonial{width:290px}
  .quote{background:var(--white);border:1px solid var(--line);padding:11px 16px 9px;font-size:7.5px;line-height:1.6;color:var(--muted)}
  .stars{color:var(--orange);font-size:12px;letter-spacing:2px;margin-top:4px}
  .avatar{width:34px;height:34px;border-radius:50%;background:linear-gradient(135deg,#d9b79a,#8c6a55);margin:8px auto 0;border:2px solid var(--white)}
  .author{font-size:8px;color:var(--ink);margin-top:5px}
  .dots{display:flex;justify-content:center;gap:5px;margin-top:10px}
  .dots span{width:14px;height:3px;background:#cfcfcf}
  .dots span.active{background:var(--orange)}

  /* Footer */
  .site-footer{height:80px;background:var(--footer);display:flex;align-items:center;justify-content:space-between;padding:0 28px}
  .footer-nav{display:flex;gap:16px;font-size:8.5px;font-weight:600;color:var(--white)}
  .copyright{font-size:7px;color:#8d8580;margin-top:7px}
  .social{display:flex;gap:7px}
  .social span{width:20px;height:20px;border:1px solid #8d8580;border-radius:50%}
</style>
</head>
<body>

<header class="site-header">
  <div class="brand"><span class="brand-square"></span>LoopVane</div>
  <nav class="main-nav">
    <span>ABOUT US</span><span>HOW IT WORK</span><span>SUPPORT</span><span>CONTACT</span>
    <span class="btn btn-nav">SIGN UP</span>
  </nav>
</header>

<section class="hero">
  <div class="hero-art" role="img" aria-label="Grey city skyline illustration with silhouettes of people, one highlighted in orange"></div>
  <div class="hero-copy">
    <h1 class="hero-title">No Smartphone, No Network</h1>
    <p class="hero-sub">We Will Help Your to Ride anywhere</p>
    <span class="btn btn-hero">CLICK HERE</span>
  </div>
  <svg class="hero-arrow left" viewBox="0 0 14 20"><path d="M11 2 3 10l8 8" fill="none" stroke="#2b2b2b" stroke-width="3"/></svg>
  <svg class="hero-arrow right" viewBox="0 0 14 20"><path d="M3 2l8 8-8 8" fill="none" stroke="#2b2b2b" stroke-width="3"/></svg>
</section>

<section class="welcome">
  <h2 class="section-title">Welcome to LoopVane</h2>
  <p class="welcome-text">LOOPVANE offers first world solutions to first world problems. These days, our smartphones are our cameras, our wallets and our ride home. LOOPVANE guarantees that even if your phone is lost or dies, you'll never get stranded again. Simply call or text (SMS) our toll-free number to request a ride.</p>
  <div class="features">
    <div class="feature">
      <span class="feature-icon"><svg width="20" height="20" viewBox="0 0 20 20"><circle cx="10" cy="6" r="4" fill="none" stroke="#2b2b2b" stroke-width="1.8"/><path d="M2 19c0-5 4-7 8-7s8 2 8 7" fill="none" stroke="#2b2b2b" stroke-width="1.8"/></svg></span>
      <div><h3 class="feature-title">Sign Up Free</h3><p class="feature-text">Create your account in a minute and set a private pin for any phone.</p></div>
    </div>
    <div class="feature">
      <span class="feature-icon"><svg width="20" height="20" viewBox="0 0 20 20"><path d="M5 2l3 4-2 2c1 2 3 4 5 5l2-2 4 3-2 3C9 17 3 11 2 4z" fill="#2b2b2b"/></svg></span>
      <div><h3 class="feature-title">Call us or SMS</h3><p class="feature-text">Dial or text our toll-free number from any phone to book a ride.</p></div>
    </div>
    <div class="feature">
      <span class="feature-icon"><svg width="22" height="18" viewBox="0 0 22 18"><path d="M4 8l2-5h10l2 5h2v6h-2v2h-3v-2H7v2H4v-2H2V8z" fill="#2b2b2b"/><circle cx="6" cy="11" r="1.3" fill="#fff"/><circle cx="16" cy="11" r="1.3" fill="#fff"/></svg></span>
      <div><h3 class="feature-title">Verifies &amp; Get Ride</h3><p class="feature-text">We confirm your pin and match you with the nearest service.</p></div>
    </div>
  </div>
</section>

<section class="why">
  <div class="why-photo" role="img" aria-label="Photo of a smiling woman leaning on a yellow taxi"></div>
  <div class="why-copy">
    <h2 class="section-title">Why Choose Us</h2>
    <p class="why-text">LOOPVANE is a heterogeneous ride-hailing service that allows users for request transportation from any "transportation network company," taxi, helicopter service, jet service or any transportation service company that is publicly available. LOOPVANE will allow users to connect through our site, automated phone system, App or any appropriated touch point available.</p>
    <span class="btn btn-why">READ MORE</span>
  </div>
</section>

<section class="testimonials">
  <h2 class="section-title">Testimonials</h2>
  <div class="testimonial-list">
    <div class="testimonial">
      <p class="quote">My phone died late at night and I still got home safely. I just called the number, entered my pin and a car arrived in minutes. Simple, fast and reliable.</p>
      <div class="stars">★★★★</div>
      <div class="avatar"></div>
      <p class="author">By Author Name, City Location</p>
    </div>
    <div class="testimonial">
      <p class="quote">I lost my phone on a trip and borrowed a stranger's to text for a ride. It was charged to my own account with no trouble at all. Great service.</p>
      <div class="stars">★★★★</div>
      <div class="avatar"></div>
      <p class="author">By Author Name, City Location</p>
    </div>
  </div>
  <div class="dots"><span class="active"></span><span></span><span></span></div>
</section>

<footer class="site-footer">
  <div>
    <nav class="footer-nav"><span>HOME</span><span>ABOUT US</span><span>HOW IT WORK</span><span>SUPPORT</span><span>CONTACT</span></nav>
    <p class="copyright">© 2017 LoopVane. All rights reserved. Terms of Use.</p>
  </div>
  <div class="social"><span></span><span></span><span></span><span></span></div>
</footer>

</body>
</html>
```